Psychiatric Office Needs a Website- 1st Time Ever!

Been in practice since 2003 with no website, but finally ready to dive in. We are Maplecrest Behavioral Healthcare, a mental health outpatient practice based in Fayetteville, Georgia that sees diverse individuals and families from childhood to advanced age for a variety of conditions. We've grown by word of mouth and referral but would now like to have a digital footprint. Be the pioneer of our website and we will be sure to share. We would like to see designs that are modern, animated, fairly colorful, easy to read, and caters to all ages. Also, we would like the design to take the whole page (not be centered) and can be viewed well on phone/tablet. Please see our outline for more information. Our motto/slogan is: Maplecrest Behavioral Healthcare- A step forward in your wellness journey, so the design should try to reflect that.
Updates

Project Deadline Extended
Reason: site in progress

Target Market(s)

Children through elderly

Industry/Entity Type

Medical

Logo Text

Stepping forward in your wellness journey

Number of Pages Required

1 page

Colors

Designer to choose colors to be used in the design.

Requirements
Must have
• Animation or moving pictures.
• Color.
• Concise.
• User friendly
• Diversity in the stock photos

```html
<!DOCTYPE html>
<html lang="en">
<head>
<meta charset="utf-8">
<title>Maplecrest Behavioral Healthcare</title>
<link href="https://fonts.googleapis.com/css2?family=Roboto:ital,wght@0,400;0,500;0,700;1,400;1,500&family=Open+Sans:ital,wght@0,400;0,600;1,400;1,600&display=swap" rel="stylesheet">
<style>
:root{
  --blue:#1e6fb0;
  --blue-dark:#1b5d97;
  --sky:#29a3de;
  --sky-light:#4fb9ea;
  --text:#333;
  --muted:#777;
  --line:#dcdcdc;
  --footer:#141414;
  --white:#fff;
}
*{box-sizing:border-box;margin:0;padding:0}
html,body{width:1200px;height:3673px;overflow:hidden}
body{font-family:"Roboto",sans-serif;color:var(--text);background:var(--white);position:relative}
.abs{position:absolute}
a{color:inherit;text-decoration:none}

/* header */
.topbar{position:absolute;top:0;left:0;width:1200px;height:95px}
.brand{position:absolute;left:98px;top:13px;display:flex;align-items:center;gap:14px}
.brand-dot{width:66px;height:66px;border-radius:50%;background:var(--sky)}
.brand-name{font-size:19px;font-weight:700;color:var(--blue)}
.brand-tag{font-size:12px;font-style:italic;color:var(--blue);margin-top:4px}
.contact-strip{position:absolute;left:555px;top:38px;font-size:14px;color:#444;display:flex;align-items:center;gap:8px}
.contact-strip svg{width:15px;height:15px}
.sep{margin:0 6px;color:#999}
.portal{position:absolute;left:938px;top:27px;width:164px;height:43px;border:2px solid var(--sky);color:var(--blue);font-size:13px;font-weight:700;display:flex;align-items:center;justify-content:center;gap:6px}
.nav{position:absolute;top:95px;left:0;width:1200px;height:42px;border-top:1px solid var(--line);border-bottom:1px solid var(--line)}
.nav a{position:absolute;top:11px;transform:translateX(-50%);font-size:16px;font-weight:500;color:#222;white-space:nowrap}
.nav a.active{color:var(--sky)}

/* hero */
.hero{position:absolute;top:137px;left:0;width:1200px;height:453px;background:linear-gradient(180deg,#5f7f9a 0%,#c79a6a 38%,#b3652f 62%,#6a3d22 82%,#3c3d3a 100%);color:var(--white);text-align:center}
.hero h1{position:absolute;top:128px;width:100%;font-size:48px;font-weight:700;letter-spacing:.5px}
.hero p{position:absolute;top:200px;width:100%;font-size:26px;font-weight:500}
.btn-ghost{position:absolute;left:500px;top:265px;width:203px;height:53px;border:2px solid var(--white);display:flex;align-items:center;justify-content:center;font-size:15px;font-weight:700;letter-spacing:.5px}
.dots{position:absolute;display:flex;gap:5px}
.dots i{width:11px;height:11px;border-radius:50%;border:1.5px solid var(--white)}
.dots i.on{background:var(--white)}

/* mission */
.mission{position:absolute;top:640px;left:0;width:1200px;text-align:center;font-family:"Open Sans",sans-serif;font-style:italic;font-weight:600;font-size:18px;line-height:34px;color:#333}
.rule{position:absolute;left:98px;top:747px;width:1004px;height:1px;background:var(--line)}

/* welcome */
.welcome h2{position:absolute;left:98px;top:838px;font-size:30px;color:var(--blue);font-weight:700}
.welcome p{position:absolute;left:98px;width:450px;font-size:13px;line-height:24px;color:#666}
.btn-outline{position:absolute;border:1.5px solid var(--blue);color:var(--blue);font-size:13px;font-weight:700;display:flex;align-items:center;justify-content:center}
.video-frame{position:absolute;left:595px;top:820px;width:495px;height:319px;border:1.5px solid #6aa3cf}
.video{position:absolute;left:622px;top:845px;width:480px;height:306px;background:linear-gradient(120deg,#c9d5dc,#9fb0bb 55%,#5d6b74);}
.play{position:absolute;left:208px;top:121px;width:64px;height:64px;border-radius:50%;background:#1a1a1a}

/* services */
.services{position:absolute;top:1242px;left:0;width:1200px;height:428px;background:linear-gradient(120deg,var(--sky-light),var(--sky) 55%,#1f8fd0);color:var(--white)}
.services h2{position:absolute;top:52px;width:100%;text-align:center;font-size:30px;font-weight:700}
.svc{position:absolute;top:126px;width:260px;text-align:center;transform:translateX(-50%)}
.svc-ring{width:160px;height:160px;border-radius:50%;border:4px solid var(--white);margin:0 auto;display:flex;align-items:center;justify-content:center}
.svc-ring span{width:108px;height:108px;border-radius:50%;background:var(--white);display:flex;align-items:center;justify-content:center}
.svc h3{margin-top:22px;font-size:16px;font-weight:700;line-height:29px}
.arrow{position:absolute;top:200px}

/* news */
.news h2{position:absolute;top:1745px;width:1200px;text-align:center;font-size:30px;color:var(--blue);font-weight:700}
.card{position:absolute;top:1832px;width:314px}
.card-img{height:196px}
.card h3{margin-top:34px;font-size:20px;font-weight:500;color:#222}
.meta{margin-top:12px;font-size:13px;color:#777;display:flex;align-items:center;gap:6px}
.meta svg{width:13px;height:13px}
.card p{margin-top:14px;font-size:13px;line-height:22px;color:#777}
.card .more{display:block;margin-top:18px;font-size:12px;font-weight:700;color:var(--blue)}

/* testimonials */
.testi{position:absolute;top:2322px;left:0;width:1200px;height:372px;background:linear-gradient(100deg,#3f6f98,#6f8ea8 45%,#c5ccd3 80%,#e2e4e6);overflow:hidden;color:var(--white)}
.testi-shape{position:absolute;left:0;top:0}
.quote-mark{position:absolute;left:95px;top:20px;font-family:"Open Sans",sans-serif;font-size:150px;font-weight:700;line-height:1}
.testi h2{position:absolute;left:98px;top:142px;font-size:30px;font-weight:700;line-height:38px}
.avatar{position:absolute;left:526px;top:53px;width:100px;height:100px;border-radius:50%;background:#8a96a0;border:4px solid var(--white)}
.testi blockquote{position:absolute;left:525px;top:180px;width:585px;font-family:"Open Sans",sans-serif;font-style:italic;font-size:16px;line-height:28px}
.testi cite{position:absolute;left:525px;top:290px;font-style:normal;font-size:16px;font-weight:500}

/* faq */
.faq h2{position:absolute;top:2790px;width:1200px;text-align:center;font-size:30px;color:var(--blue);font-weight:700}
.faq-item{position:absolute;left:167px;width:867px;height:42px;display:flex;align-items:center;font-size:18px;border:1px solid #bbb;color:#333}
.faq-item .tog{width:42px;height:42px;background:var(--blue-dark);color:var(--white);font-size:26px;font-weight:700;display:flex;align-items:center;justify-content:center;margin:-1px 14px -1px -1px}
.faq-item.open{background:var(--sky);border-color:var(--sky);color:var(--white)}
.faq-answer{position:absolute;left:167px;top:2920px;width:867px;height:57px;background:#f1f1f1;font-size:13px;color:#555;padding:20px 0 0 55px}
.faq-answer b{text-decoration:underline;font-weight:700}

/* footer */
.footer{position:absolute;top:3205px;left:0;width:1200px;height:468px}
.footer-bg{position:absolute;top:0;left:0}
.f-logo{position:absolute;left:188px;top:174px;width:90px;height:90px;border-radius:50%;background:var(--sky)}
.f-name{position:absolute;left:60px;top:283px;width:346px;text-align:center;color:var(--white);font-size:17px;font-weight:700}
.f-tag{position:absolute;left:60px;top:310px;width:346px;text-align:center;color:#ccc;font-size:12px;font-style:italic}
.f-col{position:absolute;top:170px;color:var(--white)}
.f-col h4{font-size:15px;font-weight:700;margin-bottom:16px;letter-spacing:.3px}
.f-col li{list-style:none;font-size:13px;color:#ddd;line-height:25px}
.f-col p{font-size:13px;line-height:22px;color:#ddd}
.f-input{margin-top:22px;width:253px;height:34px;background:var(--white);color:#888;font-size:12px;padding:10px 12px}
.f-btn{margin-top:25px;width:98px;height:28px;background:var(--sky);color:var(--white);font-size:11px;font-weight:700;display:flex;align-items:center;justify-content:center}
.f-contact li{display:flex;gap:16px;align-items:flex-start;margin-bottom:14px;line-height:20px}
.f-contact svg{width:15px;height:15px;margin-top:3px;flex:none}
.copy{position:absolute;left:98px;top:420px;font-size:12px;color:#ccc}
.social{position:absolute;left:978px;top:412px;display:flex;gap:8px}
.social i{width:26px;height:26px;border-radius:50%;border:1.5px solid #ddd}
</style>
</head>
<body>

<header class="topbar">
  <div class="brand">
    <div class="brand-dot"></div>
    <div>
      <div class="brand-name">Maplecrest Behavioral Healthcare</div>
      <div class="brand-tag">A step forward in your wellness journey</div>
    </div>
  </div>
  <div class="contact-strip">
    <svg viewBox="0 0 16 16"><circle cx="8" cy="8" r="6.5" fill="none" stroke="#1e6fb0" stroke-width="1.6"/><path d="M8 4v4l3 2" fill="none" stroke="#1e6fb0" stroke-width="1.6"/></svg>
    <span>Mon - Friday : 9am - 8 pm</span><span class="sep">|</span>
    <svg viewBox="0 0 16 16"><path d="M4 1.5l2.5 3-1.5 1.8c.8 1.8 2 3 3.8 3.8l1.7-1.5 3 2.5-1.5 2.5C7 13.6 2.4 9 1.5 3z" fill="#1e6fb0"/></svg>
    <span>1 800 555 0142</span>
  </div>
  <a class="portal"><svg width="12" height="12" viewBox="0 0 12 12"><circle cx="6" cy="3.5" r="2.8" fill="#1e6fb0"/><path d="M.5 12c0-3.5 2.5-5 5.5-5s5.5 1.5 5.5 5z" fill="#1e6fb0"/></svg>PATIENT PORTAL</a>
</header>

<nav class="nav">
  <a class="active" style="left:147px">Home</a>
  <a style="left:289px">About Us</a>
  <a style="left:443px">Services</a>
  <a style="left:688px">Conditions We Treat</a>
  <a style="left:855px">New Patients</a>
  <a style="left:1033px">Contact Us</a>
</nav>

<section class="hero" role="img" aria-label="City skyline behind autumn trees at sunset">
  <h1>Maplecrest Behavioral Healthcare</h1>
  <p>A step forward in your wellness journey</p>
  <a class="btn-ghost">TAKE A SCREENING</a>
  <div class="dots" style="left:572px;top:383px"><i class="on"></i><i></i><i></i><i></i></div>
</section>

<p class="mission">To be the leading provider of outpatient psychiatric care in Atlanta Metro South,<br>working together to promote (the) mental wellness of our community.</p>
<div class="rule"></div>

<section class="welcome">
  <h2>Welcome to MBHC</h2>
  <p style="top:895px">To provide mental health services to children, adults, and the developmentally disabled population that is culturally sensitive regardless of age, race, gender, orientation, religion, or creed.</p>
  <p style="top:992px">To work hand in hand with clients to overcome mental health challenges and improve their quality of life. To partner with families and caregivers in achieving desired treatment goals for the client.</p>
  <a class="btn-outline" style="left:98px;top:1102px;width:118px;height:43px">READ MORE</a>
  <div class="video-frame"></div>
  <div class="video" role="img" aria-label="Video still of a nurse with a clipboard talking with a patient in a wheelchair">
    <div class="play"><svg width="64" height="64" viewBox="0 0 64 64"><path d="M26 20l20 12-20 12z" fill="#fff"/></svg></div>
  </div>
</section>

<section class="services" role="region" aria-label="Our Services">
  <h2>Our Services</h2>
  <svg class="arrow" style="left:36px" width="18" height="30" viewBox="0 0 18 30"><path d="M15 3L4 15l11 12" fill="none" stroke="#fff" stroke-width="3"/></svg>
  <svg class="arrow" style="left:1148px" width="18" height="30" viewBox="0 0 18 30"><path d="M3 3l11 12L3 27" fill="none" stroke="#fff" stroke-width="3"/></svg>
  <div class="svc" style="left:181px">
    <div class="svc-ring"><span><svg width="50" height="50" viewBox="0 0 50 50"><rect x="6" y="10" width="32" height="32" rx="4" fill="none" stroke="#29a3de" stroke-width="4"/><path d="M20 32l2-8 18-18 6 6-18 18z" fill="#29a3de"/></svg></span></div>
    <h3>Diagnostic evaluation<br>and treatment</h3>
  </div>
  <div class="svc" style="left:460px">
    <div class="svc-ring"><span><svg width="54" height="50" viewBox="0 0 54 50"><rect x="18" y="4" width="18" height="8" fill="none" stroke="#29a3de" stroke-width="4"/><rect x="4" y="12" width="46" height="34" rx="4" fill="#29a3de"/><path d="M23 21h8v6h6v8h-6v6h-8v-6h-6v-8h6z" fill="#fff"/></svg></span></div>
    <h3>Psychopharmacology</h3>
  </div>
  <div class="svc" style="left:740px">
    <div class="svc-ring"><span><svg width="54" height="50" viewBox="0 0 54 50"><ellipse cx="27" cy="22" rx="23" ry="17" fill="none" stroke="#29a3de" stroke-width="4"/><path d="M12 34l-4 12 14-8" fill="#29a3de"/><ellipse cx="27" cy="22" rx="14" ry="8" fill="#29a3de"/></svg></span></div>
    <h3>Bariatric pre-surgical<br>consultation</h3>
  </div>
  <div class="svc" style="left:1019px">
    <div class="svc-ring"><span><svg width="44" height="54" viewBox="0 0 44 54"><path d="M4 2h24l12 12v38H4z" fill="#29a3de"/><path d="M28 2v12h12" fill="#7fcaee"/><path d="M11 24h22M11 32h22M11 40h22" stroke="#fff" stroke-width="3"/></svg></span></div>
    <h3>Disability and<br>work-related reports</h3>
  </div>
</section>

<section class="news">
  <h2>Latest News</h2>
  <article class="card" style="left:98px">
    <div class="card-img" role="img" aria-label="Doctor speaking with an older patient" style="background:linear-gradient(120deg,#eaf0f2,#c9d3d8 60%,#a9b6be)"></div>
    <h3>Finibus Bonorum et Malorum</h3>
    <div class="meta"><svg viewBox="0 0 13 13"><rect x="1" y="2" width="11" height="10" fill="#1e6fb0"/></svg>Mar 15, 2017 <span class="sep">|</span><svg viewBox="0 0 13 13"><circle cx="6.5" cy="4" r="3" fill="#1e6fb0"/><path d="M1 13c0-3 2.5-4.5 5.5-4.5S12 10 12 13z" fill="#1e6fb0"/></svg>admin</div>
    <p>At vero eos et accusamus et iusto odio dignissimos ducimus qui blanditiis praesentium voluptatum del eniti atque corrupti quos dolo.</p>
    <a class="more">READ MORE</a>
  </article>
  <article class="card" style="left:443px">
    <div class="card-img" role="img" aria-label="Researchers working in a laboratory" style="background:linear-gradient(120deg,#d9e3ea,#a7bccb 55%,#7c93a6)"></div>
    <h3>Finibus Bonorum et Malorum</h3>
    <div class="meta"><svg viewBox="0 0 13 13"><rect x="1" y="2" width="11" height="10" fill="#1e6fb0"/></svg>Mar 15, 2017 <span class="sep">|</span><svg viewBox="0 0 13 13"><circle cx="6.5" cy="4" r="3" fill="#1e6fb0"/><path d="M1 13c0-3 2.5-4.5 5.5-4.5S12 10 12 13z" fill="#1e6fb0"/></svg>admin</div>
    <p>At vero eos et accusamus et iusto odio dignissimos ducimus qui blanditiis praesentium voluptatum del eniti atque corrupti quos dolo.</p>
    <a class="more">READ MORE</a>
  </article>
  <article class="card" style="left:789px">
    <div class="card-img" role="img" aria-label="Doctor working at a laptop" style="background:linear-gradient(120deg,#f3f5f6,#d6dde1 60%,#b7c3ca)"></div>
    <h3>Finibus Bonorum et Malorum</h3>
    <div class="meta"><svg viewBox="0 0 13 13"><rect x="1" y="2" width="11" height="10" fill="#1e6fb0"/></svg>Mar 15, 2017 <span class="sep">|</span><svg viewBox="0 0 13 13"><circle cx="6.5" cy="4" r="3" fill="#1e6fb0"/><path d="M1 13c0-3 2.5-4.5 5.5-4.5S12 10 12 13z" fill="#1e6fb0"/></svg>admin</div>
    <p>At vero eos et accusamus et iusto odio dignissimos ducimus qui blanditiis praesentium voluptatum del eniti atque corrupti quos dolo.</p>
    <a class="more">READ MORE</a>
  </article>
</section>

<section class="testi" role="img" aria-label="Background of a doctor writing notes">
  <svg class="testi-shape" width="560" height="372" viewBox="0 0 560 372"><polygon points="0,0 545,0 300,372 0,372" fill="#2b78b8" opacity=".92"/></svg>
  <div class="quote-mark">&ldquo;</div>
  <h2>Client<br>Testimonials</h2>
  <div class="avatar" role="img" aria-label="Client portrait"></div>
  <blockquote>At vero eos et accusamus et iusto odio dignissimos ducimus qui blanditii praesen tium voluptatum deleniti atque corrupti quos dolores et quas molestias excepturi sint occaecati cupiditate non provident, similique sunt..</blockquote>
  <cite>- DANIEL REYES <b><i>(Manager)</i></b></cite>
  <div class="dots" style="left:1056px;top:318px"><i class="on"></i><i></i><i></i></div>
</section>

<section class="faq">
  <h2>FAQs</h2>
  <div class="faq-item open" style="top:2878px"><span class="tog">&minus;</span>What do I need to bring with me to my first visit?</div>
  <div class="faq-answer">Insurance card, patient forms found on our <b>FORM'S PAGE</b>.</div>
  <div class="faq-item" style="top:2995px"><span class="tog">+</span>How long do I have to wait to be seen?</div>
  <div class="faq-item" style="top:3054px"><span class="tog">+</span>What types of insurance do you accept?</div>
  <a class="btn-outline" style="left:519px;top:3137px;width:162px;height:47px;border-color:#999;color:var(--blue);font-size:15px">VIEW MORE</a>
</section>

<footer class="footer">
  <svg class="footer-bg" width="1200" height="468" viewBox="0 0 1200 468">
    <path d="M0 0 Q600 150 1200 0 V468 H0z" fill="#1e6fb0"/>
    <path d="M0 10 Q600 160 1200 10 V468 H0z" fill="var(--footer)"/>
    <line x1="98" y1="400" x2="1102" y2="400" stroke="#333"/>
  </svg>
  <div class="f-logo"></div>
  <div class="f-name">Maplecrest Behavioral Healthcare</div>
  <div class="f-tag">A step forward in your wellness journey</div>

  <div class="f-col" style="left:431px">
    <h4>QUICK LINKS</h4>
    <ul><li>Home</li><li>About Us</li><li>Services</li><li>Conditions We Treat</li><li>New Patients</li><li>Contact Us</li></ul>
  </div>
  <div class="f-col" style="left:612px">
    <h4>NEWSLETTER SUBSCRIPTION</h4>
    <p>Register your Email Address to get<br>Information about us</p>
    <div class="f-input">Email Address</div>
    <div class="f-btn">SUBSCRIBE</div>
  </div>
  <div class="f-col f-contact" style="left:931px">
    <h4>CONTACT US</h4>
    <ul>
      <li><svg viewBox="0 0 16 16"><path d="M8 1a5 5 0 0 1 5 5c0 4-5 9-5 9S3 10 3 6a5 5 0 0 1 5-5z" fill="#fff"/><circle cx="8" cy="6" r="2" fill="#141414"/></svg><span>2180 Linden Court,<br>Fayetteville GA 30214</span></li>
      <li><svg viewBox="0 0 16 16"><path d="M4 1.5l2.5 3-1.5 1.8c.8 1.8 2 3 3.8 3.8l1.7-1.5 3 2.5-1.5 2.5C7 13.6 2.4 9 1.5 3z" fill="#fff"/></svg><span>1 800 555 0142</span></li>
      <li><svg viewBox="0 0 16 16"><rect x="2" y="5" width="12" height="9" fill="#fff"/><rect x="4" y="1" width="8" height="4" fill="#fff"/><rect x="5" y="8" width="6" height="3" fill="#141414"/></svg><span>1 800 555 0199</span></li>
      <li><svg viewBox="0 0 16 16"><rect x="1" y="3" width="14" height="10" fill="#fff"/><path d="M1 3l7 6 7-6" fill="none" stroke="#141414" stroke-width="1.5"/></svg><span>info@maplecrestbh.com</span></li>
    </ul>
  </div>
  <div class="copy">Copyrights &copy; 2017, Maplecrest Behavioral Healthcare. All rights reserved.</div>
  <div class="social"><i></i><i></i><i></i><i></i></div>
</footer>

</body>
</html>
```